Powerpoint and Word template required

We need PowerPoint and Word templates for all of our company branded materials and stationary. We have recently rebranded our website and would like something that is reflective of our new corporate branding. A sample of some of the documents we have created recently are attached and our website is below

http://lorwynmedical.com.au/

The word template will be used for all letters we send to clients and customers and we think we want the logo and ISO 9001 cert to only appear on the first page.

The powerpoint template has to be flexible as we use this for both marketing and training purposes. I have attached a couple of samples of the types of documents we create and note that these are very basic / crude and we would be looking for something that is a significant improvement on these

In the powerpoint template it would be good to have lots of standard layouts within the template, e.g. different 'standard layouts for multiple elements on a page including pictures and text etc.
Updates

Project Deadline Extended
Reason: Still looking for a professional yet modern template and important to us that we can see more tan just a title slide and the layout of the other slide master slides is very important to us. Many thanks, Dale

Industry/Entity Type

Healthcare

Font styles to use
Sans Serif

Colors
33a6d7

Requirements
Must have
• Templates must be versatile for use; powerpoint template must be able to be used for training materials and weel as marketing / pitch books.
• Word template must be able to be used as a basis for our corporate letter head through to RFP response type documents as well as Reference / Operating manual type of documents
• In terms of the design it must be consistent with our new corporate image which is best represented by our new website design; www.lorwynmedical.com

```html
<!DOCTYPE html>
<html lang="en">
<head>
<meta charset="utf-8">
<title>Issues to Consider When Prescribing an APAM – Lorwyn</title>
<link rel="stylesheet" href="https://fonts.googleapis.com/css2?family=Roboto+Condensed:wght@400;700&display=swap">
<style>
  :root {
    --brand-blue: #2f8fd3;
    --brand-blue-deep: #2a86cc;
    --text-grey: #666a70;
    --footer-grey: #555a60;
    --rule-grey: #c5ccd3;
    --page-dark: #26282b;
    --sky-top: #eef4fa;
    --sky-mid: #e4eef7;
    --sky-low: #d5e3ef;
    --white: #ffffff;
  }
  * { margin: 0; padding: 0; box-sizing: border-box; }
  html, body { width: 1200px; height: 900px; overflow: hidden; }
  body { font-family: "Roboto Condensed", "Arial Narrow", sans-serif; }

  .slide {
    position: relative;
    width: 1200px;
    height: 900px;
    overflow: hidden;
  }
  .slide-backdrop {
    position: absolute;
    inset: 0;
    background:
      radial-gradient(ellipse 70% 30% at 30% 60%, rgba(255,255,255,0.7), transparent 70%),
      radial-gradient(ellipse 60% 25% at 75% 85%, rgba(255,255,255,0.55), transparent 70%),
      linear-gradient(180deg, var(--sky-top) 0%, var(--sky-mid) 55%, var(--sky-low) 100%);
  }

  .slide-title {
    position: absolute;
    left: 21px;
    top: 28px;
    font-size: 30px;
    font-weight: 700;
    color: var(--brand-blue);
    letter-spacing: 0.2px;
    white-space: pre;
  }
  .title-rule {
    position: absolute;
    left: 0;
    top: 68px;
    width: 732px;
    height: 3px;
    background: var(--rule-grey);
  }

  .brand {
    position: absolute;
    left: 944px;
    top: 30px;
    display: flex;
    align-items: center;
    gap: 12px;
  }
  .brand-mark {
    width: 46px;
    height: 46px;
    background: var(--brand-blue);
    border-radius: 4px;
  }
  .brand-name {
    font-size: 52px;
    font-weight: 400;
    color: var(--brand-blue);
    line-height: 1;
  }

  .issue-list {
    position: absolute;
    top: 150px;
    list-style: none;
  }
  .issue-list.col-left { left: 62px; }
  .issue-list.col-right { left: 648px; }
  .issue-list li {
    display: flex;
    align-items: center;
    height: 66px;
    font-size: 27px;
    font-weight: 700;
    color: var(--text-grey);
    white-space: nowrap;
  }
  .issue-list li::before {
    content: "";
    flex: 0 0 33px;
    height: 33px;
    margin-right: 22px;
    background: var(--brand-blue-deep);
    border-radius: 4px;
  }

  .copyright {
    position: absolute;
    left: 0;
    top: 837px;
    width: 198px;
    height: 48px;
    background: var(--brand-blue);
    color: var(--white);
    font-size: 20px;
    display: flex;
    align-items: center;
    justify-content: center;
  }
  .footer-url {
    position: absolute;
    left: 0;
    right: 0;
    top: 848px;
    text-align: center;
    font-size: 20px;
    color: var(--footer-grey);
    padding-left: 30px;
    word-spacing: 4px;
  }
  .page-number {
    position: absolute;
    left: 1146px;
    top: 849px;
    width: 42px;
    height: 42px;
    background: var(--page-dark);
    color: var(--white);
    border-radius: 5px;
    font-size: 20px;
    font-weight: 700;
    display: flex;
    align-items: center;
    justify-content: center;
  }
</style>
</head>
<body>
  <main class="slide">
    <div class="slide-backdrop" role="img" aria-label="Soft pale blue sky with light clouds as slide background"></div>

    <h1 class="slide-title">ISSUES TO CONSIDER WHEN PRESCRIBING AN  APAM</h1>
    <div class="title-rule"></div>

    <div class="brand">
      <span class="brand-mark"></span>
      <span class="brand-name">Lorwyn</span>
    </div>

    <ul class="issue-list col-left">
      <li>DEGREE OF BED MOBILITY.</li>
      <li>WEIGHT OF PATIENT.</li>
      <li>SENSATION</li>
      <li>LOCATION OF PRESSURE ULCER.</li>
      <li>STAGE OF PRESSURE INJURY.</li>
      <li>EVALUATION OF RISK ASSESSMENT</li>
      <li>CONTINUOUS EVALUATION</li>
      <li>PREVIOUS HISTORY</li>
      <li>SKIN INTEGRITY</li>
    </ul>

    <ul class="issue-list col-right">
      <li>DEGREE OF BED MOBILITY.</li>
      <li>WEIGHT OF PATIENT.</li>
      <li>SENSATION</li>
      <li>LOCATION OF PRESSURE ULCER.</li>
      <li>STAGE OF PRESSURE INJURY.</li>
      <li>EVALUATION OF RISK ASSESSMENT</li>
      <li>CONTINUOUS EVALUATION</li>
      <li>PREVIOUS HISTORY</li>
      <li>SKIN INTEGRITY</li>
    </ul>

    <footer>
      <div class="copyright">Copyright text here</div>
      <div class="footer-url">||&nbsp; www.lorwynmedical.com.au &nbsp;||</div>
      <div class="page-number">01</div>
    </footer>
  </main>
</body>
</html>
```